Fire Risk Assessment App needs a sleek UI design

I need a sleek, modern but professional design for my 5 page Fire Risk Assessment App. Include gradient background, fire themed colours including reds, yellows, light orange and a touch of black. Design must ooze simplicity and professionalism. This is for the UK market. See attached images and word doc for more information.

Target Market(s)

General public and business owners

Industry/Entity Type

Technology / Fire Safety

Colors
00AB8E
00BBA5
67D7C9
C6EFE9
E9F9F6
59FF00
82FF00
B8FF75
E3FFCB
F4FFEA
FFC000
F8CF3A
FAE287
FDF2CF
FEFAEE
F0912C
F2A743
F7CA91
FBE8D2
FDF5EE
EE7325
F08F49
F5BC92
FAE3D3
FDF4ED
EB3D1F
EC4F4E
F09395
F8D3D4
FCEDEE

```html
<!DOCTYPE html>
<html lang="en">
<head>
<meta charset="utf-8">
<title>Fire Risk Assessment App – Screens</title>
<link href="https://fonts.googleapis.com/css2?family=Figtree:wght@400;500;600&display=swap" rel="stylesheet">
<style>
:root{
  --stage:#20223a;
  --stage-word:#272a44;
  --cream-top:#fef8e6;
  --cream-bottom:#fbe5b0;
  --ink:#1d1d24;
  --muted:#55514a;
  --red:#eb3d1f;
  --orange:#ee7325;
  --amber:#f0912c;
  --gold:#ffc000;
  --green:#59ff00;
  --teal:#00ab8e;
  --card:#fff9ea;
  --nav:#f6e2ad;
}
*{box-sizing:border-box;margin:0;padding:0}
html,body{width:1200px;height:1200px;overflow:hidden}
body{background:var(--stage);font-family:"Figtree",sans-serif;color:var(--ink);position:relative}
.backdrop-word{position:absolute;left:68px;top:990px;font-size:138px;font-weight:500;color:var(--stage-word);white-space:nowrap;letter-spacing:6px;line-height:1}
.screen{position:absolute;width:232px;height:502px;overflow:hidden;background:linear-gradient(180deg,var(--cream-top) 0%,#fdf1cf 55%,var(--cream-bottom) 100%)}
.abs{position:absolute}
.center{left:0;right:0;text-align:center}
.title{font-size:16px;font-weight:400;line-height:18px}
.sub{font-size:8.5px;color:var(--muted)}
.accent{color:var(--red);font-weight:600}
.nav{position:absolute;left:0;bottom:0;width:232px;height:42px;background:linear-gradient(180deg,#fbeec6,var(--nav))}
.nav-mark{position:absolute;top:0;width:26px;height:2px;border-radius:2px;background:var(--red)}
.nav svg{position:absolute;top:14px;width:13px;height:13px}
.btn-pill{position:absolute;height:29px;border-radius:15px;display:flex;align-items:center;justify-content:center;font-size:9px}
.btn-fill{background:linear-gradient(90deg,var(--red),var(--amber));color:#fff;box-shadow:0 4px 8px rgba(238,115,37,.35)}
.btn-line{border:1px solid var(--red);background:#fff8e8;color:var(--ink)}
.btn-dot{position:absolute;left:2px;top:2px;width:25px;height:25px;border-radius:50%;background:linear-gradient(135deg,var(--gold),var(--orange));display:flex;align-items:center;justify-content:center}
.ring{position:absolute;left:45px;top:72px;width:142px;height:142px;border-radius:50%;border:10px solid rgba(248,207,58,.12)}
.plus-btn{position:absolute;left:77px;top:104px;width:78px;height:78px;border-radius:50%;background:radial-gradient(circle at 40% 35%,var(--gold),var(--amber) 60%,var(--orange));box-shadow:0 8px 16px rgba(238,115,37,.4);display:flex;align-items:center;justify-content:center}
.tab{position:absolute;top:207px;font-size:9px;color:var(--muted);transform:translateX(-50%)}
.tab.on{color:var(--red);font-weight:500}
.item{position:absolute;left:11px;width:212px;height:42px;border-radius:9px;background:var(--card);padding:7px 10px}
.item b{display:block;font-size:9px;font-weight:500}
.item span{display:block;font-size:8.5px;color:var(--muted);margin-top:3px}
.tick{position:absolute;right:10px;top:13px;width:13px;height:13px;border-radius:50%;background:var(--green);display:flex;align-items:center;justify-content:center}
.pct{position:absolute;right:10px;top:10px;width:21px;height:21px;border-radius:50%;background:#fff;font-size:6px;display:flex;align-items:center;justify-content:center;border:2px solid #eee;border-top-color:var(--green);border-right-color:var(--green)}
.section-label{position:absolute;left:10px;top:339px;font-size:9px;color:var(--red);font-weight:500}
.buy{position:absolute;top:366px;width:106px;height:71px;border-radius:9px;background:var(--card);padding:12px 10px}
.buy b{display:block;font-size:9px;font-weight:500;line-height:10.5px}
.buy span{display:block;font-size:8.5px;color:var(--muted);line-height:10.5px;margin-top:4px}
.pay-panel{position:absolute;left:11px;top:77px;width:212px;height:370px;border-radius:13px;background:linear-gradient(160deg,var(--amber),var(--orange) 55%,var(--red))}
.pay-title{position:absolute;top:17px;left:0;right:0;text-align:center;color:#fff;font-size:9.5px;line-height:12px;font-weight:500}
.plan{position:absolute;left:10px;width:191px;height:62px;border-radius:8px;background:rgba(255,255,255,.15);color:#fff}
.plan .radio{position:absolute;left:9px;top:11px;width:15px;height:15px;border-radius:50%;border:1.5px solid rgba(255,255,255,.75)}
.plan b{position:absolute;left:31px;top:8px;font-size:8.5px;font-weight:500}
.plan small{position:absolute;left:31px;top:21px;font-size:6px;opacity:.85}
.plan i{position:absolute;right:9px;top:13px;font-style:normal;font-size:8.5px;font-weight:600}
.plan .save{position:absolute;left:31px;top:36px;width:151px;height:18px;border-radius:5px;background:rgba(255,255,255,.18);font-size:6.5px;display:flex;align-items:center;justify-content:center}
.q-head{position:absolute;left:11px;top:34px;width:212px;height:102px;border-radius:10px;background:linear-gradient(135deg,var(--amber),var(--orange) 60%,var(--red));color:#fff;padding:12px 16px}
.q-head p{font-size:8.5px;line-height:12.5px}
.q-head hr{border:0;border-top:1px solid rgba(255,255,255,.3);margin:8px 0}
.q-head .cl{font-size:8px;font-weight:600}
.q-head .cl span{display:block;font-weight:400}
.bolt{position:absolute;width:36px;height:36px;border-radius:50%;background:radial-gradient(circle at 40% 35%,var(--gold),var(--orange));box-shadow:0 4px 10px rgba(238,115,37,.45);display:flex;align-items:center;justify-content:center;z-index:2}
.q-card{position:absolute;left:11px;top:162px;width:212px;height:284px;border-radius:10px;background:rgba(255,250,235,.85)}
.opts{position:absolute;left:16px;top:73px;width:180px;height:31px;display:flex;gap:3px}
.opt{flex:1;background:#fff;border-radius:5px;font-size:7.5px;display:flex;flex-direction:column;align-items:center;justify-content:center;gap:3px}
.opt.sel{border:1px solid var(--amber)}
.opt.wide{flex:1.35}
.dot{width:8px;height:8px;border-radius:50%}
.answer{position:absolute;left:16px;top:115px;width:180px;height:20px;border-radius:5px;background:#fff;font-size:7.5px;color:var(--muted);display:flex;align-items:center;justify-content:center}
.photo{position:absolute;left:16px;top:145px;width:180px;height:82px;border-radius:6px;background:linear-gradient(135deg,#8f8f8f,#d9d9d9 55%,#9a9a9a)}
.msg{position:absolute;left:10px;top:77px;width:212px;height:127px;border-radius:9px;border:1px solid #f1dcae;background:rgba(255,252,242,.7);padding:14px 15px;font-size:8px;color:var(--muted)}
.mic{position:absolute;right:8px;bottom:8px;width:25px;height:25px;border-radius:50%;background:linear-gradient(135deg,var(--gold),var(--orange));display:flex;align-items:center;justify-content:center}
.flames{position:absolute;left:0;top:300px;width:232px;height:160px;background:radial-gradient(ellipse at 50% 100%,rgba(240,145,44,.28),rgba(248,207,58,.12) 55%,transparent 75%)}
.hero-art{position:absolute;left:10px;top:98px;width:212px;height:232px;border-radius:14px;background:radial-gradient(ellipse at 50% 50%,rgba(238,115,37,.55),rgba(240,145,44,.3) 45%,rgba(248,207,58,.12) 70%,transparent 85%)}
</style>
</head>
<body>

<div class="backdrop-word">Fire Assessment</div>

<!-- Welcome -->
<section class="screen" style="left:99px;top:80px">
  <div class="abs center title" style="top:33px">The Most <span class="accent">User Friendly</span><br>Fire Risk Assessment App<br>Available</div>
  <div class="hero-art" role="img" aria-label="Illustration of fanned assessment cards showing a fire hazard question with flames behind"></div>
  <div class="abs center sub" style="top:341px;font-size:9px">Quick tap response and voice activated typing</div>
  <div class="btn-pill btn-fill" style="left:42px;top:361px;width:149px">
    <div class="btn-dot"><svg width="10" height="10" viewBox="0 0 10 10"><circle cx="4" cy="3" r="2" fill="#fff"/><path d="M0 9c0-3 8-3 8 0z" fill="#fff"/></svg></div>Create a Free Account</div>
  <div class="abs center sub" style="top:407px;font-size:9px;color:var(--ink)">Any <span style="color:var(--red)">responsible person</span> can do it.</div>
  <div class="btn-pill btn-line" style="left:42px;top:429px;width:149px">
    <div class="btn-dot"><svg width="10" height="10" viewBox="0 0 10 10"><circle cx="4" cy="3" r="2" fill="#fff"/><path d="M0 9c0-3 8-3 8 0z" fill="#fff"/></svg></div>Customer Login</div>
  <div class="abs center sub" style="top:471px;font-size:7.5px">Create and endorsed by Veteran Fire Officers</div>
</section>

<!-- Dashboard completed -->
<section class="screen" style="left:355px;top:80px">
  <div class="abs center title" style="top:33px">Dashboard</div>
  <div class="abs center sub" style="top:53px">Start Fire Assessment</div>
  <div class="ring"></div>
  <div class="plus-btn"><svg width="16" height="16" viewBox="0 0 16 16"><path d="M8 1v14M1 8h14" stroke="#fff" stroke-width="3" stroke-linecap="round"/></svg></div>
  <div class="tab on" style="left:83px">Completed</div>
  <div class="tab" style="left:151px">In Progress</div>
  <div class="item" style="top:234px"><b>Rowan’s Barbershop</b><span>Lorem Ipsum is simply dummy text</span><div class="tick"><svg width="7" height="7" viewBox="0 0 7 7"><path d="M1 3.5 3 5.5 6 1.5" stroke="#fff" stroke-width="1.3" fill="none"/></svg></div></div>
  <div class="item" style="top:283px"><b>Rowan’s Barbershop</b><span>Lorem Ipsum is simply dummy text</span><div class="tick"><svg width="7" height="7" viewBox="0 0 7 7"><path d="M1 3.5 3 5.5 6 1.5" stroke="#fff" stroke-width="1.3" fill="none"/></svg></div></div>
  <div class="section-label">Purchases</div>
  <div class="buy" style="left:11px"><b>Residential Fire Risk Assessment</b><span>Lorem Ipsum is sim ply dummy text</span></div>
  <div class="buy" style="left:124px"><b>Commercial Fire Risk Assessment</b><span>Lorem Ipsum is sim ply dummy text</span></div>
  <nav class="nav"><div class="nav-mark" style="left:18px"></div>
    <svg style="left:24px" viewBox="0 0 13 13"><rect x="0" y="0" width="5" height="5" rx="1" fill="var(--orange)"/><rect x="7" y="0" width="5" height="5" rx="1" fill="var(--orange)"/><rect x="0" y="7" width="5" height="5" rx="1" fill="var(--orange)"/><path d="M7 8h6M7 11h6" stroke="var(--orange)" stroke-width="1.5"/></svg>
    <svg style="left:82px" viewBox="0 0 13 13"><rect x="0" y="2" width="13" height="10" rx="2" fill="#20223a"/><path d="M0 5h13" stroke="#f6e2ad" stroke-width="1.5"/></svg>
    <svg style="left:139px" viewBox="0 0 13 13"><path d="M2 1h9a2 2 0 0 1 2 2v5a2 2 0 0 1-2 2H6l-3 3v-3H2a2 2 0 0 1-2-2V3a2 2 0 0 1 2-2z" fill="#20223a"/><path d="M4 5.5h5" stroke="#f6e2ad" stroke-width="1.3"/></svg>
    <svg style="left:196px" viewBox="0 0 13 13"><path d="M6.5 0 12 3v7l-5.5 3L1 10V3z" fill="#20223a"/><circle cx="6.5" cy="5" r="1.7" fill="#f6e2ad"/><path d="M3.5 9.5c1-2 5-2 6 0" stroke="#f6e2ad" stroke-width="1.3" fill="none"/></svg>
  </nav>
</section>

<!-- Dashboard in progress -->
<section class="screen" style="left:612px;top:80px">
  <div class="abs center title" style="top:33px">Dashboard</div>
  <div class="abs center sub" style="top:53px">Start Fire Assessment</div>
  <div class="ring"></div>
  <div class="plus-btn"><svg width="16" height="16" viewBox="0 0 16 16"><path d="M8 1v14M1 8h14" stroke="#fff" stroke-width="3" stroke-linecap="round"/></svg></div>
  <div class="tab" style="left:82px">Completed</div>
  <div class="tab on" style="left:150px">In Progress</div>
  <div class="item" style="top:234px;height:44px"><b>Elm Road School</b><span>Lorem Ipsum is simply dummy text</span><div class="pct">30%</div></div>
  <div class="item" style="top:287px;height:44px"><b>Willow Bank Care Home</b><span>Lorem Ipsum is simply dummy text</span><div class="pct">40%</div></div>
  <div class="section-label">Purchases</div>
  <div class="buy" style="left:10px"><b>Residential Fire Risk Assessment</b><span>Lorem Ipsum is sim ply dummy text</span></div>
  <div class="buy" style="left:124px"><b>Commercial Fire Risk Assessment</b><span>Lorem Ipsum is sim ply dummy text</span></div>
  <nav class="nav"><div class="nav-mark" style="left:18px"></div>
    <svg style="left:24px" viewBox="0 0 13 13"><rect x="0" y="0" width="5" height="5" rx="1" fill="var(--orange)"/><rect x="7" y="0" width="5" height="5" rx="1" fill="var(--orange)"/><rect x="0" y="7" width="5" height="5" rx="1" fill="var(--orange)"/><path d="M7 8h6M7 11h6" stroke="var(--orange)" stroke-width="1.5"/></svg>
    <svg style="left:82px" viewBox="0 0 13 13"><rect x="0" y="2" width="13" height="10" rx="2" fill="#20223a"/><path d="M0 5h13" stroke="#f6e2ad" stroke-width="1.5"/></svg>
    <svg style="left:139px" viewBox="0 0 13 13"><path d="M2 1h9a2 2 0 0 1 2 2v5a2 2 0 0 1-2 2H6l-3 3v-3H2a2 2 0 0 1-2-2V3a2 2 0 0 1 2-2z" fill="#20223a"/><path d="M4 5.5h5" stroke="#f6e2ad" stroke-width="1.3"/></svg>
    <svg style="left:196px" viewBox="0 0 13 13"><path d="M6.5 0 12 3v7l-5.5 3L1 10V3z" fill="#20223a"/><circle cx="6.5" cy="5" r="1.7" fill="#f6e2ad"/><path d="M3.5 9.5c1-2 5-2 6 0" stroke="#f6e2ad" stroke-width="1.3" fill="none"/></svg>
  </nav>
</section>

<!-- Purchase -->
<section class="screen" style="left:869px;top:80px">
  <div class="abs center title" style="top:33px">Purchase</div>
  <div class="abs center sub" style="top:53px">Lorem Ipsum is simply dummy text</div>
  <div class="pay-panel">
    <div class="pay-title">FIRE RISK ASSESSMENT<br>PAYMENT OPTIONS</div>
    <div class="plan" style="top:50px"><div class="radio"></div><b>Bronze 1</b><small>Lorem Ipsum is sim ply dummy</small><i>€19.99</i><div class="save">Save</div></div>
    <div class="plan" style="top:118px"><div class="radio"></div><b>Silver 3</b><small>Lorem Ipsum is sim ply dummy</small><i>€54.99</i><div class="save">Save</div></div>
    <div class="plan" style="top:186px"><div class="radio"></div><b>Gold 5</b><small>Lorem Ipsum is sim ply dummy</small><i>€89.99</i><div class="save">Save</div></div>
    <div class="plan" style="top:254px"><div class="radio"></div><b>Platinum 10</b><small>Lorem Ipsum is sim ply dummy</small><i>€174.99</i><div class="save">Save</div></div>
    <div class="btn-pill btn-fill" style="left:10px;top:328px;width:191px">
      <div class="btn-dot"><svg width="10" height="10" viewBox="0 0 10 10"><circle cx="5" cy="5" r="4.5" fill="#fff"/><text x="5" y="7.5" font-size="7" text-anchor="middle" fill="#ee7325" font-family="Figtree,sans-serif">$</text></svg></div>Checkout</div>
  </div>
  <nav class="nav"><div class="nav-mark" style="left:75px"></div>
    <svg style="left:24px" viewBox="0 0 13 13"><rect x="0" y="0" width="5" height="5" rx="1" fill="#20223a"/><rect x="7" y="0" width="5" height="5" rx="1" fill="#20223a"/><rect x="0" y="7" width="5" height="5" rx="1" fill="#20223a"/><path d="M7 8h6M7 11h6" stroke="#20223a" stroke-width="1.5"/></svg>
    <svg style="left:82px" viewBox="0 0 13 13"><rect x="0" y="2" width="13" height="10" rx="2" fill="var(--orange)"/><path d="M0 5h13" stroke="#f6e2ad" stroke-width="1.5"/></svg>
    <svg style="left:139px" viewBox="0 0 13 13"><path d="M2 1h9a2 2 0 0 1 2 2v5a2 2 0 0 1-2 2H6l-3 3v-3H2a2 2 0 0 1-2-2V3a2 2 0 0 1 2-2z" fill="#20223a"/><path d="M4 5.5h5" stroke="#f6e2ad" stroke-width="1.3"/></svg>
    <svg style="left:196px" viewBox="0 0 13 13"><path d="M6.5 0 12 3v7l-5.5 3L1 10V3z" fill="#20223a"/><circle cx="6.5" cy="5" r="1.7" fill="#f6e2ad"/><path d="M3.5 9.5c1-2 5-2 6 0" stroke="#f6e2ad" stroke-width="1.3" fill="none"/></svg>
  </nav>
</section>

<!-- Question -->
<section class="screen" style="left:355px;top:617px">
  <div class="q-head">
    <p>Fire Risk Assessment<br>Fire Hazards<br>Section: 7.00/30.00</p>
    <div class="abs" style="right:16px;top:12px;width:26px;height:26px;border-radius:50%;background:#fff;color:var(--ink);font-size:7.5px;display:flex;align-items:center;justify-content:center;border:2px solid #fff;border-top-color:var(--green);border-right-color:var(--green)">30%</div>
    <hr>
    <p class="cl">ELECTRONIC SOURCES OF IGNITION<span>(Clause 13 &amp; Annex B)</span></p>
    <div class="abs" style="right:16px;top:70px;width:24px;height:24px;border-radius:50%;background:#fff;border:2px solid var(--green)"></div>
  </div>
  <div class="bolt" style="left:98px;top:144px"><svg width="12" height="16" viewBox="0 0 9 12"><path d="M5 0 0 7h4l-1 5 6-8H5z" fill="#1d1d24"/></svg></div>
  <div class="q-card">
    <p class="abs" style="left:16px;top:28px;font-size:7.5px">Q: 7.01</p>
    <p class="abs" style="left:16px;top:41px;font-size:9.5px;line-height:12px;width:160px">Are resonable measure taken to prevent fire of electrical origin?</p>
    <div class="opts">
      <div class="opt"><span class="dot" style="background:var(--teal)"></span>Yes</div>
      <div class="opt"><span class="dot" style="background:var(--red)"></span>No</div>
      <div class="opt sel"><span class="dot" style="background:var(--amber)"></span>(N/A)</div>
      <div class="opt wide"><span class="dot" style="background:var(--gold);border-radius:2px"></span>Camera</div>
      <div class="opt"><span class="dot" style="background:var(--orange)"></span>Mic</div>
    </div>
    <div class="answer">No, electric sockets are overloaded</div>
    <div class="photo" role="img" aria-label="Photo of an open electrical fuse box with fire and smoke"></div>
    <div class="btn-pill btn-line" style="left:16px;top:242px;width:85px;padding-left:18px">
      <div class="btn-dot"><svg width="10" height="10" viewBox="0 0 10 10"><path d="M3 2 1 4l2 2M1 4h5a3 3 0 0 1 0 6H4" stroke="#fff" stroke-width="1.2" fill="none"/></svg></div>Save &amp; Exit</div>
    <div class="btn-pill btn-fill" style="left:109px;top:242px;width:86px;padding-right:16px">Next
      <div class="btn-dot" style="left:auto;right:2px"><svg width="10" height="10" viewBox="0 0 10 10"><path d="M1 5h8M6 2l3 3-3 3" stroke="#fff" stroke-width="1.2" fill="none"/></svg></div></div>
  </div>
  <nav class="nav">
    <svg style="left:24px" viewBox="0 0 13 13"><rect x="0" y="0" width="5" height="5" rx="1" fill="#20223a"/><rect x="7" y="0" width="5" height="5" rx="1" fill="#20223a"/><rect x="0" y="7" width="5" height="5" rx="1" fill="#20223a"/><path d="M7 8h6M7 11h6" stroke="#20223a" stroke-width="1.5"/></svg>
    <svg style="left:82px" viewBox="0 0 13 13"><rect x="0" y="2" width="13" height="10" rx="2" fill="#20223a"/><path d="M0 5h13" stroke="#f6e2ad" stroke-width="1.5"/></svg>
    <svg style="left:139px" viewBox="0 0 13 13"><path d="M2 1h9a2 2 0 0 1 2 2v5a2 2 0 0 1-2 2H6l-3 3v-3H2a2 2 0 0 1-2-2V3a2 2 0 0 1 2-2z" fill="#20223a"/><path d="M4 5.5h5" stroke="#f6e2ad" stroke-width="1.3"/></svg>
    <svg style="left:196px" viewBox="0 0 13 13"><path d="M6.5 0 12 3v7l-5.5 3L1 10V3z" fill="#20223a"/><circle cx="6.5" cy="5" r="1.7" fill="#f6e2ad"/><path d="M3.5 9.5c1-2 5-2 6 0" stroke="#f6e2ad" stroke-width="1.3" fill="none"/></svg>
  </nav>
</section>

<!-- Technical support -->
<section class="screen" style="left:612px;top:617px">
  <div class="abs center title" style="top:33px">Technical Support</div>
  <div class="abs center sub" style="top:53px">Type/Record Your Response Here</div>
  <div class="msg">Write your message here...
    <div class="mic"><svg width="8" height="10" viewBox="0 0 8 10"><rect x="2" y="0" width="4" height="7" rx="2" fill="#fff"/></svg></div></div>
  <div class="btn-pill btn-fill" style="left:10px;top:213px;width:212px">
    <div class="btn-dot"><svg width="10" height="10" viewBox="0 0 10 10"><path d="M9 1 1 4.5l3 1 1 3z" fill="#fff"/></svg></div>Send</div>
  <div class="flames" role="img" aria-label="Soft flame illustration fading into the background"></div>
  <nav class="nav"><div class="nav-mark" style="left:132px"></div>
    <svg style="left:24px" viewBox="0 0 13 13"><rect x="0" y="0" width="5" height="5" rx="1" fill="#20223a"/><rect x="7" y="0" width="5" height="5" rx="1" fill="#20223a"/><rect x="0" y="7" width="5" height="5" rx="1" fill="#20223a"/><path d="M7 8h6M7 11h6" stroke="#20223a" stroke-width="1.5"/></svg>
    <svg style="left:82px" viewBox="0 0 13 13"><rect x="0" y="2" width="13" height="10" rx="2" fill="#20223a"/><path d="M0 5h13" stroke="#f6e2ad" stroke-width="1.5"/></svg>
    <svg style="left:139px" viewBox="0 0 13 13"><path d="M2 1h9a2 2 0 0 1 2 2v5a2 2 0 0 1-2 2H6l-3 3v-3H2a2 2 0 0 1-2-2V3a2 2 0 0 1 2-2z" fill="var(--orange)"/><path d="M4 5.5h5" stroke="#f6e2ad" stroke-width="1.3"/></svg>
    <svg style="left:196px" viewBox="0 0 13 13"><path d="M6.5 0 12 3v7l-5.5 3L1 10V3z" fill="#20223a"/><circle cx="6.5" cy="5" r="1.7" fill="#f6e2ad"/><path d="M3.5 9.5c1-2 5-2 6 0" stroke="#f6e2ad" stroke-width="1.3" fill="none"/></svg>
  </nav>
</section>

</body>
</html>
```